Business Card Design Project

Keep it simple , using logo and colors that compliment. Logo on one side with complimentary back ground color. Other side, personal info with possible complimentary design/colors

Target Market(s)

we are a non for profit that will be seeking donations . Both monetary and in kind

Industry/Entity Type

Business

Font styles to use
Sans Serif

Colors

Designer to choose colors to be used in the design.

```html
<!DOCTYPE html>
<html lang="en">
<head>
<meta charset="utf-8">
<title>Bright Path Fund – Business Card</title>
<link rel="stylesheet" href="https://fonts.googleapis.com/css2?family=Lato:wght@400;700;900&display=swap">
<style>
  :root {
    --backdrop: #2b2b2d;
    --card: #1d2341;
    --card-edge: #262d52;
    --accent: #e3d11c;
    --text-light: #e6e8f0;
    --text-muted: #a2a8c0;
  }
  * { box-sizing: border-box; margin: 0; padding: 0; }
  html, body {
    width: 1200px;
    height: 997px;
    overflow: hidden;
    background: var(--backdrop);
    font-family: "Lato", Arial, sans-serif;
  }
  .stage {
    position: relative;
    width: 1200px;
    height: 997px;
  }
  .card {
    position: absolute;
    width: 600px;
    height: 340px;
    border-radius: 26px;
    background: linear-gradient(160deg, var(--card-edge), var(--card) 60%);
    box-shadow: 0 18px 40px rgba(0, 0, 0, 0.45);
  }
  .card--front { left: 90px; top: 70px; }
  .card--back { left: 510px; top: 470px; }

  .brand {
    display: flex;
    align-items: center;
    gap: 14px;
    color: var(--accent);
    font-weight: 400;
  }
  .brand__dot {
    border: 4px solid var(--accent);
    border-radius: 50%;
  }
  .card--front .brand {
    position: absolute;
    inset: 0;
    justify-content: center;
    font-size: 40px;
  }
  .card--front .brand__dot { width: 40px; height: 40px; }

  .card--back .brand {
    position: absolute;
    right: 40px;
    top: 52px;
    font-size: 28px;
  }
  .card--back .brand__dot { width: 30px; height: 30px; border-width: 3px; }

  .person {
    position: absolute;
    left: 40px;
    top: 128px;
  }
  .person__name {
    color: var(--accent);
    font-weight: 900;
    font-size: 20px;
    letter-spacing: 0.5px;
    text-transform: uppercase;
  }
  .person__role {
    color: var(--text-light);
    font-weight: 700;
    font-size: 14px;
    letter-spacing: 0.6px;
    text-transform: uppercase;
    margin-top: 3px;
  }

  .address {
    position: absolute;
    right: 40px;
    top: 200px;
    color: var(--text-muted);
    font-size: 14px;
    line-height: 1.45;
    text-align: left;
  }

  .contacts {
    position: absolute;
    left: 40px;
    bottom: 34px;
    list-style: none;
    color: var(--text-light);
    font-size: 15px;
    font-weight: 700;
  }
  .contacts li {
    display: flex;
    align-items: center;
    gap: 12px;
    height: 26px;
  }
  .contacts svg {
    width: 16px;
    height: 16px;
    fill: var(--accent);
    flex: none;
  }
</style>
</head>
<body>
<main class="stage">

  <section class="card card--front" aria-label="Card front">
    <div class="brand">
      <span class="brand__dot"></span>
      <span class="brand__name">Bright Path Fund</span>
    </div>
  </section>

  <section class="card card--back" aria-label="Card back">
    <div class="brand">
      <span class="brand__dot"></span>
      <span class="brand__name">Bright Path Fund</span>
    </div>

    <div class="person">
      <p class="person__name">Jonas Weber</p>
      <p class="person__role">Owner &amp; Director</p>
    </div>

    <address class="address">
      Lindenweg 12<br>
      60311 Frankfurt am Main
    </address>

    <ul class="contacts">
      <li>
        <svg viewBox="0 0 16 16" aria-hidden="true"><path d="M1 5c0-2 2-3 7-3s7 1 7 3v1.5h-3.5V5h-7v1.5H1zM4 7h8l2 7H2z"/></svg>
        <span>0049 170 2284915</span>
      </li>
      <li>
        <svg viewBox="0 0 16 16" aria-hidden="true"><path d="M4 1h8v4H4zM1 6h14v6h-3v3H4v-3H1zM5 10v4h6v-4z"/></svg>
        <span>0049 170 2284900</span>
      </li>
      <li>
        <svg viewBox="0 0 16 16" aria-hidden="true"><path d="M1 3h14v1.5L8 9 1 4.5zM1 6l7 4.5L15 6v7H1z"/></svg>
        <span>jonas.weber@brightpathfund.org</span>
      </li>
      <li>
        <svg viewBox="0 0 16 16" aria-hidden="true"><path d="M6.5 9.5l3-3 1 1-3 3zM3 9l2-2 1.2 1.2-2 2a1.4 1.4 0 0 0 2 2l2-2L9.4 11.4l-2 2A3.1 3.1 0 0 1 3 9zM7 4.6l2-2A3.1 3.1 0 0 1 13.4 7l-2 2-1.2-1.2 2-2a1.4 1.4 0 0 0-2-2l-2 2z"/></svg>
        <span>www.brightpathfund.org</span>
      </li>
    </ul>
  </section>

</main>
</body>
</html>
```